We need a business card design, letterhead design and envelope design for our corporate image

We are looking for a corporate business card design, letterhead and envelope design to match the business card design. Logo is done.

```html
<!DOCTYPE html>
<html lang="en">
<head>
<meta charset="utf-8">
<title>Halvorn Business Card</title>
<link rel="stylesheet" href="https://fonts.googleapis.com/css2?family=Open+Sans:ital,wght@0,400;0,700;1,400;1,700&display=swap">
<style>
  :root {
    --page-bg: #2a2a2a;
    --card-black: #1b1b1b;
    --accent-yellow: #ffc600;
    --text-white: #f2f2f2;
    --brand-faint: #2b2b2b;
  }
  * { margin: 0; padding: 0; box-sizing: border-box; }
  html, body { width: 1200px; height: 900px; overflow: hidden; }
  body {
    background: var(--page-bg);
    font-family: "Open Sans", Arial, sans-serif;
    position: relative;
  }
  .card {
    position: absolute;
    left: 300px;
    width: 600px;
    height: 343px;
    background: var(--card-black);
    border-bottom: 6px solid var(--accent-yellow);
    box-shadow: 0 12px 30px rgba(0,0,0,0.45);
  }
  .card--front { top: 70px; }
  .card--back { top: 480px; }

  .brand {
    position: absolute;
    font-weight: 700;
    white-space: nowrap;
  }
  .card--front .brand {
    left: 40px; width: 258px; top: 142px;
    text-align: center;
    font-size: 40px;
    line-height: 1.2;
    color: var(--text-white);
  }
  .card--back .brand {
    left: 0; right: 0; top: 124px;
    text-align: center;
    font-size: 64px;
    line-height: 1.2;
    color: var(--brand-faint);
  }

  .divider {
    position: absolute;
    left: 318px; top: 70px;
    width: 1px; height: 200px;
    background: var(--accent-yellow);
  }
  .contact {
    position: absolute;
    left: 340px; top: 70px;
    color: var(--text-white);
    font-size: 13.5px;
    line-height: 1.45;
  }
  .contact__name {
    color: var(--accent-yellow);
    font-weight: 700;
    font-style: italic;
    font-size: 17px;
    letter-spacing: 0.5px;
    text-transform: uppercase;
  }
  .contact__role { font-style: italic; margin-bottom: 10px; }
  .contact__address { margin-bottom: 12px; }
  .contact__line { display: flex; align-items: center; gap: 8px; }
  .contact__icon { width: 12px; height: 12px; flex: none; }
</style>
</head>
<body>
  <section class="card card--front">
    <div class="brand">Halvorn</div>
    <div class="divider"></div>
    <div class="contact">
      <p class="contact__name">Daniel Reyes</p>
      <p class="contact__role">President</p>
      <p class="contact__address">1870 Seacliff Harbor Way<br>Bayview CA 90410</p>
      <p class="contact__line">
        <svg class="contact__icon" viewBox="0 0 12 12" aria-hidden="true"><path d="M2.5 1 L4.5 1 L5.3 3.5 L4 4.5 Q5 7 7.5 8 L8.5 6.7 L11 7.5 L11 9.5 Q11 11 9.5 11 Q1 10 1 2.5 Q1 1 2.5 1Z" fill="var(--accent-yellow)"/></svg>
        555-018-2047
      </p>
      <p class="contact__line">
        <svg class="contact__icon" viewBox="0 0 12 12" aria-hidden="true"><rect x="0.5" y="2.5" width="11" height="7" fill="var(--accent-yellow)"/><path d="M0.5 2.5 L6 6.5 L11.5 2.5" stroke="var(--card-black)" stroke-width="1" fill="none"/></svg>
        dreyes@halvorn.com
      </p>
      <p class="contact__line">
        <svg class="contact__icon" viewBox="0 0 12 12" aria-hidden="true"><circle cx="6" cy="6" r="5.2" fill="none" stroke="var(--accent-yellow)" stroke-width="1.2"/><ellipse cx="6" cy="6" rx="2.2" ry="5.2" fill="none" stroke="var(--accent-yellow)" stroke-width="1"/><line x1="0.8" y1="6" x2="11.2" y2="6" stroke="var(--accent-yellow)" stroke-width="1"/></svg>
        www.halvorn.com
      </p>
    </div>
  </section>

  <section class="card card--back">
    <div class="brand">Halvorn</div>
  </section>
</body>
</html>
```